Cyber Security firm working in the Financial Services sector needs a brochure

We need a brochure covering our products and offerings. We work exclusively with Independent Broker Dealers, their Reps and RIAs in the US. We help them keep their computers secure and compliant with applicable regulations and policies. Have attached samples of our logo an descriptions of our products and services.

Target Market(s)

Financial Institutions and Financial Advisors

Industry/Entity Type

Financial Service

```html
<!DOCTYPE html>
<html lang="en">
<head>
<meta charset="utf-8">
<title>Secure Lens Services Brochure</title>
<link href="https://fonts.googleapis.com/css2?family=Roboto+Condensed:wght@400;700&family=Roboto:wght@400&display=swap" rel="stylesheet">
<style>
  :root {
    --navy: #1d3f8f;
    --blue: #2c5bb0;
    --band: #3563b8;
    --sky: #cfe3f6;
    --ice: #f3f8fd;
    --ink: #1c1c22;
    --heading: #1a3a8c;
    --icon: #8a8d92;
    --stage: #e7e9ec;
  }
  html, body {
    margin: 0;
    width: 1200px;
    height: 1200px;
    overflow: hidden;
    background: var(--stage);
  }
  .page {
    position: absolute;
    left: 152px;
    top: 20px;
    width: 896px;
    height: 1160px;
    overflow: hidden;
    background:
      radial-gradient(ellipse 70% 40% at 80% 60%, #ffffff 0%, rgba(255,255,255,0) 70%),
      linear-gradient(160deg, var(--ice) 0%, var(--sky) 55%, #e6f0fa 75%, var(--sky) 100%);
    box-shadow: 0 6px 24px rgba(0,0,0,.25);
    font-family: "Roboto", Arial, sans-serif;
    color: var(--ink);
  }
  .masthead {
    position: relative;
    height: 278px;
    background: linear-gradient(180deg, var(--band) 0%, var(--band) 38%, #2a55ad 38%, var(--navy) 100%);
  }
  .masthead::after {
    content: "";
    position: absolute;
    right: 50px;
    bottom: -34px;
    border-left: 20px solid transparent;
    border-right: 20px solid transparent;
    border-top: 34px solid var(--navy);
  }
  .brand {
    position: absolute;
    left: 50%;
    top: -52px;
    width: 214px;
    height: 214px;
    margin-left: -107px;
    border-radius: 50%;
    background: #fff;
    display: flex;
    align-items: center;
    justify-content: center;
    padding-top: 52px;
    box-sizing: border-box;
  }
  .brand-name {
    font-family: "Roboto Condensed", Arial, sans-serif;
    font-weight: 700;
    font-size: 30px;
    color: var(--navy);
    letter-spacing: .5px;
  }
  .intro {
    position: absolute;
    left: 42px;
    right: 38px;
    top: 172px;
    margin: 0;
    font-family: "Roboto Condensed", Arial, sans-serif;
    font-size: 18.4px;
    line-height: 23.3px;
    color: #fff;
  }
  .services {
    position: relative;
    padding: 24px 38px 0 182px;
  }
  .service { position: relative; margin-bottom: 10px; }
  .service h2 {
    margin: 0 0 10px;
    font-family: "Roboto Condensed", Arial, sans-serif;
    font-weight: 700;
    font-size: 19px;
    color: var(--heading);
  }
  .service p {
    margin: 0 0 12px;
    font-size: 12.9px;
    line-height: 16.9px;
    text-align: justify;
  }
  .service-icon {
    position: absolute;
    left: -150px;
    top: 6px;
    width: 100px;
    height: 90px;
    border-radius: 14px;
    background: var(--icon);
    opacity: .85;
  }
  .gap-lg { margin-top: 22px; }
  .footer-band {
    position: absolute;
    left: 0;
    bottom: 0;
    width: 100%;
    height: 40px;
  }
</style>
</head>
<body>
  <article class="page">
    <header class="masthead">
      <div class="brand"><span class="brand-name">Secure Lens</span></div>
      <p class="intro">Secure Lens provides Computer Security support and services to the Broker Dealer and Independent Advisor community. We have been providing these services for over eight years and our team has decades of experience in the Financial Services sector. We currently support, monitor and inspect thousands of Advisors and their devices across multiple Broker Dealers and RIAs. Below is a list of our most popular services.</p>
    </header>

    <section class="services">
      <div class="service">
        <div class="service-icon" role="img" aria-label="Backup database icon"></div>
        <h2>Managed Backup</h2>
        <p>We partner with Harlowmere Storage owned Quillfen Backup Pro to provide backup services. This provides encrypted transmission and storage in SSAE 16 audited and ISO 27001 certified facilities for your back-up needs. We help you configure the back-ups, monitor them on a daily basis and are are there to help if you need to do any restores. Price $1 per GB per month.</p>
      </div>
      <div class="service">
        <div class="service-icon" role="img" aria-label="Shield with magnifier icon"></div>
        <h2>Managed Anti-Virus</h2>
        <p>Correctly functioning and up-to-date Anti-Virus (AV) software is a requirement for all computers connected to the internet. With only one or two computers it is relatively easy to stay on top of the situation. However, once you get more than a couple of computers and users knowing their condition becomes more difficult without centralized reporting and monitoring. Our managed AV solution provides a centralized portal for monitoring and reporting. We are notified of any issues, whether it's a virus detected or an issue with the AV itself. This software and service is available for $52 per user per year with a one time set up fee or $25 per device. The advantage of the per user fee is, if a user has both a desktop and a laptop, both will be covered for the $52 per year.</p>
      </div>
      <div class="service">
        <div class="service-icon" role="img" aria-label="Laptop with tools icon"></div>
        <h2>Managed Software Patching</h2>
        <p>Keeping computers up-to-date with all critical security patches is an important component in protecting your infrastructure. An effective Patch Management strategy requires timely application of patches. Our patching functions in a closed loop environment. We push the necessary patches to the computers and then use our monitoring system at the device level to verify all have been successfully applied.</p>
        <p>This solution is quite effective for distributed environments with limited local cyber security expertise as well as small offices which prefer to outsource this requirement. Price $3.99 per month per computer. Requires Computer Security Monitoring.</p>
      </div>
      <div class="service">
        <div class="service-icon" role="img" aria-label="Encrypted drive icon"></div>
        <h2>Whole Disk Encryption</h2>
        <p>We remotely access your computer and perform whole disk encryption as required by your Broker Dealer. We can also help you select the most appropriate encryption methodology for your specific environment. Pricing from $95 per computer.</p>
      </div>
      <div class="service">
        <div class="service-icon" role="img" aria-label="Monitor with shield icon" style="top:40px"></div>
        <h2>Computer Security Monitoring</h2>
        <p>We monitor the security status of your computer on a daily basis. We detect if any new software was installed and if it appears to be dangerous we contact you to discuss the ramifications. We monitor the security patch levels of key software and compare your status to that required by your BD. If there are security fixes available for your computer, we provide you with the necessary information and help get those applied. We also check the status of your anti-virus and disk encryption to make sure it is within guidelines. Pricing $8 per computer per month.</p>
      </div>
      <div class="service gap-lg">
        <h2>New Computer Sourcing</h2>
        <p>We are an authorized Northfield Value Added Reseller and will be happy to help you get your new computer. We work with you to determine an appropriate configuration and what would be a good fit for your specific needs.</p>
      </div>
      <div class="service">
        <div class="service-icon" role="img" aria-label="Gear with power symbol icon" style="top:-40px"></div>
        <h2>New Computer Configuration</h2>
        <p>Configuration services provided for new computers. These can be sourced from us or locally and shipped to us or done remotely. Price $300.</p>
      </div>
    </section>

    <svg class="footer-band" viewBox="0 0 896 40" preserveAspectRatio="none" aria-hidden="true">
      <defs>
        <linearGradient id="bandFill" x1="0" x2="1">
          <stop offset="0" stop-color="#5fa3e0"/>
          <stop offset="1" stop-color="#1d3f8f"/>
        </linearGradient>
      </defs>
      <polygon points="0,40 896,8 896,40" fill="url(#bandFill)"/>
    </svg>
  </article>
</body>
</html>
```